Letterhead for Business Law Firm

We need a letter head for our firm based on the design we have settled on and it is attached. Our clients are small and large businesses around the world, and our letterhead is used typically for formal legal purposes such as demand letters (accusing the recipient of doing bad things) or responding to demand letters. It may also be sent to regulators and other government agencies. So this needs to be tasteful, but a little edgy as well - we try to convey that we are a firm that is different - businesses and investors come to us for creative, quick advice, typically in high stress circumstances, and for our ability to work through high conflict situations, and rapid paced engagements.

Target Market(s)

Lawyers, business executives, investors, government regulators who may receive letters from this firm on behalf of its clients.

Industry/Entity Type

Business

Requirements
Must have
• The design and the firm's contact information:
• Thornwell Law Firm, P.C.
• 1876 NE 57th Ave
• Portland, OR 97213
• phone: 971 555 0147
• fax: 971 555 0182
• in what placement and how depicted (e.g. a phone icon instead of the word "phone") I leave to your creative ideas.
Nice to have
• design and information can be placed at the top, bottom and/or sides of the letter, and the design should be for a standard letter size paper - and can have a separate design for the second page.

```html
<!DOCTYPE html>
<html lang="en">
<head>
<meta charset="utf-8">
<title>Thornwell Law Firm, P.C. — Letterhead</title>
<link href="https://fonts.googleapis.com/css2?family=Source+Sans+3:wght@400;600&display=swap" rel="stylesheet">
<style>
  :root {
    --paper: #ffffff;
    --ink: #1c1a1b;
    --teal: #3f6e7a;
    --white: #ffffff;
  }
  html, body {
    margin: 0;
    padding: 0;
    width: 933px;
    height: 1200px;
    overflow: hidden;
    background: var(--paper);
  }
  .letterhead {
    position: relative;
    width: 933px;
    height: 1200px;
    background: var(--paper);
    font-family: "Source Sans 3", "Myriad Pro", sans-serif;
    color: var(--ink);
  }
  .brand {
    position: absolute;
    top: 28px;
    left: 0;
    width: 100%;
    display: flex;
    justify-content: center;
    align-items: center;
    gap: 12px;
  }
  .brand-mark {
    width: 14px;
    height: 14px;
    background: var(--teal);
  }
  .brand-name {
    font-size: 38px;
    font-weight: 400;
    letter-spacing: 10px;
    text-transform: uppercase;
    color: var(--teal);
    line-height: 62px;
  }
  .footer {
    position: absolute;
    left: 0;
    width: 100%;
    top: 1105px;
  }
  .rule {
    height: 3px;
    background: var(--ink);
  }
  .contact-band {
    margin-top: 2px;
    height: 38px;
    background: var(--teal);
    display: flex;
    justify-content: center;
    align-items: center;
    gap: 9px;
    color: var(--white);
    font-size: 17px;
  }
  .contact-item {
    display: flex;
    align-items: center;
    gap: 5px;
  }
  .contact-item svg {
    width: 14px;
    height: 14px;
    fill: none;
    stroke: var(--white);
    stroke-width: 1.6;
  }
  .band-gap {
    height: 5px;
  }
  .address {
    display: flex;
    justify-content: center;
    align-items: center;
    gap: 6px;
    margin-top: 10px;
    font-size: 17px;
    color: #3a3a3a;
  }
  .address svg {
    width: 16px;
    height: 14px;
    fill: none;
    stroke: var(--teal);
    stroke-width: 1.6;
  }
</style>
</head>
<body>
<main class="letterhead">
  <header class="brand">
    <span class="brand-mark"></span>
    <span class="brand-name">Thornwell</span>
  </header>

  <footer class="footer">
    <div class="rule"></div>
    <div class="contact-band">
      <span class="contact-item">
        <svg viewBox="0 0 16 16"><circle cx="8" cy="8" r="6.6"/><path d="M5.6 4.6c-.6 2.8 1.2 6 4.4 6.8l.8-1.4-1.4-.9-.8.7c-1-.5-1.8-1.6-2-2.7l.9-.6-.6-1.6z"/></svg>
        971-555-0147
      </span>
      <span class="contact-item">
        <svg viewBox="0 0 16 16"><rect x="4.5" y="1.5" width="7" height="13" rx="1"/><path d="M6 4h4M6 7h1M9 7h1M6 9.5h1M9 9.5h1M6 12h1M9 12h1"/></svg>
        971-555-0182
      </span>
      <span class="contact-item">
        <svg viewBox="0 0 16 16"><path d="M1.5 6.5 8 2.5l6.5 4v7h-13z"/><path d="M1.5 6.5 8 10.5l6.5-4"/></svg>
        info@thornwelllaw.com
      </span>
      <span class="contact-item">
        <svg viewBox="0 0 16 16"><circle cx="8" cy="8" r="6.5"/><ellipse cx="8" cy="8" rx="3" ry="6.5"/><path d="M1.5 8h13M2.6 4.7h10.8M2.6 11.3h10.8"/></svg>
        www.thornwelllaw.com
      </span>
    </div>
    <div class="band-gap"></div>
    <div class="rule"></div>
    <div class="address">
      <svg viewBox="0 0 18 16"><path d="M1 6 9 1.5 17 6M2.5 6v8.5h13V6M2.5 9h13M2.5 12h13M1 14.5h16"/></svg>
      1876 NE 57th Ave, Portland, OR 97213
    </div>
  </footer>
</main>
</body>
</html>
```